Veranix - Solution provider in business consulting

Veranix is a swiss based company providing solutions for developing markets. The business covers various fields of business consulting, such as supply chain, product costs, quality management and manufacturing management. The Business operates in a efficient, straight and solution oriented manner.
The final design should communicate these characteristics. Asian people as well as as western people shall identify the qualities of the company at first sight.
The customer needs business cards with a simple view but an recognizable design, printed in high quality. Engraved elements such as the globe or simple words are possible.
Available colors are: (RAL)
102/102/102
51/102/102
153/204/153
255/102/51
Font: Calibri

```html
<!DOCTYPE html>
<html lang="en">
<head>
<meta charset="utf-8">
<title>Veranix Business Card</title>
<link href="https://fonts.googleapis.com/css2?family=Carlito:wght@400;700&display=swap" rel="stylesheet">
<style>
  :root {
    --page-bg: #d9d6d0;
    --back-grey: #a3a3a3;
    --back-grey-dark: #8f8f8f;
    --panel-grey: #666666;
    --card-white: #ffffff;
    --globe-fill: #e6e6e6;
    --globe-edge: #f6f6f6;
    --logo-dark: #5a5a5a;
    --text-light: #ffffff;
    --text-soft: #e8e8e8;
  }
  * { margin: 0; padding: 0; box-sizing: border-box; }
  html, body {
    width: 1200px; height: 950px; overflow: hidden;
    background: var(--page-bg);
    font-family: "Carlito", "Calibri", sans-serif;
  }
  .canvas { position: relative; width: 1200px; height: 950px; }
  .card {
    position: absolute; left: 260px; width: 680px; height: 400px;
    border-radius: 4px; overflow: hidden;
    box-shadow: 0 10px 28px rgba(0,0,0,0.25);
  }
  .card-back {
    top: 55px;
    background: linear-gradient(160deg, var(--back-grey) 0%, var(--back-grey-dark) 100%);
  }
  .back-brand {
    position: absolute; left: 0; right: 0; top: 150px;
    text-align: center; color: var(--text-light);
    font-size: 66px; font-weight: 400; letter-spacing: 1px;
  }
  .back-web {
    position: absolute; left: 0; right: 0; top: 290px;
    text-align: center; color: var(--text-light);
    font-size: 15px; letter-spacing: 5px;
  }
  .card-front { top: 495px; background: var(--card-white); }
  .front-art { position: absolute; inset: 0; }
  .front-brand {
    position: absolute; left: 330px; top: 118px; width: 200px;
    text-align: center; color: var(--logo-dark);
    font-size: 50px; font-weight: 400; letter-spacing: 1px;
  }
  .person { position: absolute; left: 40px; top: 190px; color: var(--text-light); }
  .person-name { font-size: 24px; font-weight: 700; }
  .person-role { font-size: 15px; color: var(--text-soft); margin-top: 2px; }
  .contact { position: absolute; left: 40px; top: 262px; color: var(--text-light); font-size: 14.5px; line-height: 17px; }
  .company-name { font-weight: 700; }
  .contact-list { list-style: none; margin-top: 3px; }
  .contact-list li { display: flex; align-items: center; gap: 6px; }
  .contact-icon { width: 13px; height: 13px; flex: none; }
</style>
</head>
<body>
<main class="canvas">

  <section class="card card-back" aria-label="Business card back">
    <p class="back-brand">veranix</p>
    <p class="back-web">www.veranix.ch</p>
  </section>

  <section class="card card-front" aria-label="Business card front">
    <svg class="front-art" width="680" height="400" viewBox="0 0 680 400" aria-hidden="true">
      <rect x="0" y="0" width="680" height="400" fill="var(--card-white)"/>
      <rect x="0" y="0" width="430" height="400" fill="var(--panel-grey)"/>
      <circle cx="430" cy="150" r="192" fill="var(--globe-fill)" stroke="var(--globe-edge)" stroke-width="8"/>
    </svg>

    <p class="front-brand">veranix</p>

    <div class="person">
      <p class="person-name">Marco Keller</p>
      <p class="person-role">CEO</p>
    </div>

    <address class="contact" style="font-style:normal">
      <p class="company-name">Veranix GmbH</p>
      <p>Lindenweg 14, 9000 Talbach</p>
      <p>Switzerland</p>
      <ul class="contact-list">
        <li>
          <svg class="contact-icon" viewBox="0 0 16 16" aria-hidden="true"><path d="M3 2h3l1 4-2 1a9 9 0 0 0 4 4l1-2 4 1v3a1 1 0 0 1-1 1A13 13 0 0 1 2 3a1 1 0 0 1 1-1z" fill="#fff"/></svg>
          +41 71 555 0142
        </li>
        <li>
          <svg class="contact-icon" viewBox="0 0 16 16" aria-hidden="true"><rect x="4" y="1" width="8" height="14" rx="1.5" fill="none" stroke="#fff" stroke-width="1.6"/><circle cx="8" cy="12.5" r="0.9" fill="#fff"/></svg>
          +41 79 555 0187
        </li>
        <li>
          <svg class="contact-icon" viewBox="0 0 16 16" aria-hidden="true"><rect x="1" y="3" width="14" height="10" fill="#fff"/><path d="M1 3l7 6 7-6" fill="none" stroke="#666" stroke-width="1.3"/></svg>
          marco.keller@veranix.ch
        </li>
        <li>
          <svg class="contact-icon" viewBox="0 0 16 16" aria-hidden="true"><circle cx="8" cy="8" r="6.5" fill="none" stroke="#fff" stroke-width="1.4"/><path d="M1.5 8h13M8 1.5c-3 3.5-3 9.5 0 13M8 1.5c3 3.5 3 9.5 0 13" fill="none" stroke="#fff" stroke-width="1"/></svg>
          www.veranix.ch
        </li>
      </ul>
    </address>
  </section>

</main>
</body>
</html>
```